QP Fiduciary Website Redesign Contest

We want to refresh our website to be more insitutional, professional for an international audience. We have designed a new logo for this purpose and that has been attached. A full brand brief and positioning statement has also been attached. Please read through all the documents carefully before designing. The old website is found here: https://qp-fiduciary.example/

Target Market(s)

Actuaries and associated businesses internationally

Industry/Entity Type

professional services - actuaries

Number of Pages Required

3 page

Font styles to use
Sans Serif

Colors
0054AA
0677BA
7BADD7
CADEEF
E8F1F8
0094D4
00A9DD
6FCCEA
C7EBF8
E9F6FB
F0912C
F2A743
F7CA91
FBE8D2
FDF5EE
EE7325
F08F49
F5BC92
FAE3D3
FDF4ED
EB3D1F
EC4F4E
F09395
F8D3D4
FCEDEE

Requirements
Must have
• blues and greens to match the logo color, complimentary colors, navigation
Nice to have
• old site: https://qp-fiduciary.example/

```html
<!DOCTYPE html>
<html lang="en">
<head>
<meta charset="utf-8">
<title>QP Fiduciary — Actuarial Software</title>
<link href="https://fonts.googleapis.com/css2?family=Inter:wght@400;500;600;700;800&family=Archivo:wght@700;800&display=swap" rel="stylesheet">
<style>
:root{
  --navy:#0b2e86;
  --blue:#0054AA;
  --blue-mid:#0677BA;
  --blue-soft:#7BADD7;
  --blue-pale:#CADEEF;
  --blue-mist:#E8F1F8;
  --sky:#0094D4;
  --orange:#EE7325;
  --orange-deep:#E1521F;
  --orange-soft:#F08F49;
  --amber:#F0912C;
  --ink:#111111;
  --text:#555b66;
  --white:#ffffff;
  --heading:"Archivo",Arial,sans-serif;
  --body:"Inter",Arial,sans-serif;
}
*{box-sizing:border-box;margin:0;padding:0}
html,body{width:1200px;height:4967px;overflow:hidden}
body{position:relative;font-family:var(--body);color:var(--text);background:var(--white)}
.abs{position:absolute}
.btn{position:absolute;display:flex;align-items:center;justify-content:center;border-radius:24px;background:var(--orange-deep);color:var(--white);font-size:15px;font-weight:600;text-decoration:none}
.section-title{position:absolute;left:0;width:1200px;text-align:center;font-family:var(--heading);font-weight:800;color:var(--ink);font-size:42px;letter-spacing:.3px}
.section-lead{position:absolute;left:300px;width:600px;text-align:center;font-size:16px;line-height:29px;color:var(--text)}

/* header */
.site-header{position:absolute;top:0;left:0;width:1200px;height:135px;background:var(--white);border-top:4px solid var(--orange);box-shadow:0 2px 10px rgba(0,0,0,.06);z-index:5}
.brand{position:absolute;left:110px;top:48px;display:flex;align-items:center;gap:12px;font-family:var(--body);font-weight:700;font-size:34px;color:var(--navy);letter-spacing:1px}
.brand-dot{width:30px;height:30px;border-radius:50%;background:var(--blue)}
.header-cta{left:672px;top:32px;width:262px;height:42px;background:var(--navy);font-size:14px;font-weight:500}
.client-login{left:950px;top:32px;width:136px;height:42px;background:var(--white);color:var(--navy);box-shadow:0 2px 10px rgba(0,40,120,.18);font-size:14px;font-weight:500}
.main-nav{position:absolute;top:92px;left:510px;display:flex;gap:0;font-size:14px;color:#222}
.main-nav a{color:inherit;text-decoration:none;position:absolute;white-space:nowrap}
.main-nav .active{color:var(--orange);font-weight:600}

/* hero */
.hero{position:absolute;top:135px;left:0;width:1200px;height:740px}
.hero svg{position:absolute;inset:0}
.hero-title{position:absolute;left:110px;top:130px;font-family:var(--heading);font-weight:800;color:var(--white);line-height:1}
.hero-title .l1{display:block;font-size:54px;letter-spacing:1px}
.hero-title .l2{display:block;font-size:74px;margin-top:8px;letter-spacing:1px}
.hero-sub{position:absolute;left:110px;top:270px;font-family:var(--heading);font-weight:700;font-size:27px;line-height:38px;color:var(--white)}
.hero-text{position:absolute;left:110px;top:356px;width:460px;font-size:16px;line-height:28px;color:#eef3fb}
.hero-btn{left:110px;top:460px;width:306px;height:40px}

/* overview */
.overview-feature{position:absolute;width:260px}
.overview-feature h3{font-size:16px;font-weight:700;color:var(--blue-mid);letter-spacing:.3px;margin-bottom:6px}
.overview-feature p{font-size:13.5px;line-height:23px;color:var(--text)}
.feature-left{text-align:right}
.feature-icon{position:absolute;width:70px;height:70px;border-radius:50%;background:var(--blue-mist);display:flex;align-items:center;justify-content:center;box-shadow:0 4px 12px rgba(0,84,170,.12)}
.hub-ring{position:absolute;left:448px;top:1176px;width:304px;height:304px;border-radius:50%;background:var(--white);box-shadow:0 8px 40px rgba(0,60,140,.15)}
.hub-core{position:absolute;left:488px;top:1216px;width:224px;height:224px;border-radius:50%;background:radial-gradient(circle at 35% 30%,#2a78d6,#0b3a9e 70%);display:flex;align-items:center;justify-content:center;color:var(--white);font-weight:700;font-size:26px}

/* solutions */
.solution-card{position:absolute;top:1852px;width:311px;height:348px;border-radius:26px;background:var(--white);box-shadow:0 6px 24px rgba(0,40,100,.12);text-align:center;padding:0 40px}
.solution-card.featured{border:1.5px solid var(--navy);border-bottom:5px solid var(--navy)}
.solution-icon{width:86px;height:86px;border-radius:50%;margin:56px auto 0;background:radial-gradient(circle at 35% 30%,#2a78d6,#0b3a9e 75%);display:flex;align-items:center;justify-content:center}
.solution-card h3{margin-top:26px;font-size:16.5px;font-weight:700;color:var(--navy);line-height:27px;letter-spacing:.3px}
.solution-card p{margin-top:10px;font-size:13.5px;line-height:26px;color:var(--text)}

/* characteristics */
.characteristics{position:absolute;top:2320px;left:0;width:1200px;height:772px}
.characteristics svg.band{position:absolute;inset:0}
.visual-circle{position:absolute;left:112px;top:214px;width:452px;height:452px;border-radius:50%;background:radial-gradient(circle at 50% 45%,#3b6fd8 0%,#1b2f7a 45%,#0a1238 100%);box-shadow:0 10px 30px rgba(0,0,0,.25)}
.char-title{position:absolute;left:629px;top:246px;font-family:var(--heading);font-weight:800;font-size:42px;line-height:58px;color:var(--white)}
.char-list{position:absolute;left:629px;top:375px;width:458px;list-style:none}
.char-list li{position:relative;padding-left:40px;font-size:19px;line-height:30px;color:var(--white);margin-bottom:30px}
.char-list svg{position:absolute;left:2px;top:5px}

/* insights */
.insight-card{position:absolute;top:3352px;width:307px;height:444px;border-radius:22px;background:var(--white);box-shadow:0 6px 24px rgba(0,40,100,.12);overflow:hidden;border:1px solid #f3d9c8}
.insight-card.featured{border:1.5px solid var(--orange)}
.insight-media{height:247px;border-radius:20px 20px 0 0;margin:4px 4px 0}
.date-pill{display:inline-flex;align-items:center;gap:7px;margin:30px 0 0 22px;height:34px;padding:0 16px;border-radius:18px;background:var(--orange-deep);color:var(--white);font-size:12px}
.insight-card h3{margin:12px 22px 0;font-size:16px;font-weight:600;line-height:26px;color:#1c1c1c}
.insight-card p{margin:8px 22px 0;font-size:13.5px;line-height:23px;color:var(--text)}

/* cta */
.cta-icon{position:absolute;left:536px;top:3985px;width:128px;height:128px;border-radius:50%;background:radial-gradient(circle at 35% 30%,#2a78d6,#0b3a9e 75%);box-shadow:0 0 0 8px var(--white),0 6px 24px rgba(0,40,120,.25)}
.cta-title{top:4140px;line-height:50px}

/* footer */
.site-footer{position:absolute;top:4460px;left:0;width:1200px;height:507px}
.site-footer svg{position:absolute;inset:0}
.footer-brand{position:absolute;top:162px;left:0;width:1200px;text-align:center;font-weight:700;font-size:42px;letter-spacing:2px;color:var(--white)}
.footer-nav{position:absolute;top:262px;left:0;width:1200px;font-size:15px;font-weight:500;color:var(--white)}
.footer-nav span{position:absolute}
.contact{position:absolute;top:326px;display:flex;gap:14px;align-items:center;color:var(--white);font-size:14px;line-height:25px}
.contact-icon{width:38px;height:38px;border-radius:50%;background:var(--orange-deep);display:flex;align-items:center;justify-content:center;flex:none}
.follow-btn{left:496px;top:414px;width:210px;height:42px;background:var(--white);color:var(--navy);font-size:14px}
.copyright{position:absolute;top:476px;left:0;width:1200px;text-align:center;font-size:12px;color:var(--white)}
</style>
</head>
<body>

<header class="site-header">
  <div class="brand"><span class="brand-dot"></span>QP Fiduciary</div>
  <a class="btn header-cta" href="#">Request Technical Walkthrough</a>
  <a class="btn client-login" href="#">Client Login</a>
  <nav class="main-nav">
    <a class="active" style="left:0">HOME</a>
    <a style="left:92px">Platform</a>
    <a style="left:199px">Solutions</a>
    <a style="left:307px">Insights</a>
    <a style="left:410px">Company</a>
    <a style="left:524px">Contact</a>
  </nav>
</header>

<section class="hero">
  <svg width="1200" height="740" viewBox="0 0 1200 740">
    <defs>
      <linearGradient id="heroBlue" x1="0" y1="0" x2="1" y2="1">
        <stop offset="0" stop-color="#2f6fc0"/>
        <stop offset=".55" stop-color="#1d58a8"/>
        <stop offset="1" stop-color="#0c3787"/>
      </linearGradient>
      <linearGradient id="heroOrange" x1="0" y1="0" x2="1" y2="0">
        <stop offset="0" stop-color="#E1521F"/>
        <stop offset=".6" stop-color="#EE7325"/>
        <stop offset="1" stop-color="#F0912C"/>
      </linearGradient>
    </defs>
    <path d="M0 0H1200V380C1100 500 960 620 760 660C560 690 360 660 0 520Z" fill="url(#heroBlue)"/>
    <path d="M600 0C720 160 820 300 1200 240V0Z" fill="#4a86cf" opacity=".35"/>
    <path d="M520 0C640 260 820 420 1200 330V300C860 380 700 250 600 0Z" fill="#d9e8f8" opacity=".35"/>
    <path d="M800 0C880 200 1000 300 1200 300V180C1060 190 940 120 880 0Z" fill="#0c3787" opacity=".35"/>
    <path d="M160 610C380 700 620 720 820 660C1000 600 1120 500 1200 400V470C1100 590 960 690 780 730C560 770 360 730 160 610Z" fill="url(#heroOrange)"/>
    <path d="M220 650C420 700 620 700 800 670C980 630 1110 540 1200 450V470C1110 570 980 660 790 700C600 735 420 720 220 650Z" fill="#F2A743" opacity=".7"/>
  </svg>
  <h1 class="hero-title"><span class="l1">ACTUARIAL</span><span class="l2">SOFTWARE</span></h1>
  <p class="hero-sub">FOR STRUCTURED, AUDITABLE<br>FINANCIAL ANALYSIS</p>
  <p class="hero-text">Software that translates actuarial methodologies into disciplined decision-ready analytical tools across diverse regulatory environments.</p>
  <a class="btn hero-btn" href="#">Request a Technical Walkthrough</a>
</section>

<h2 class="section-title" style="top:958px">PLATFORM OVERVIEW</h2>
<p class="section-lead" style="top:1014px">QP Fiduciary develops modular actuarial software designed to support reserving, valuation, pricing, and risk analysis workflows across diverse regulatory environments.</p>

<div class="hub-ring"></div>
<div class="hub-core">QP Fiduciary</div>

<div class="overview-feature feature-left" style="left:128px;top:1133px"><h3>DATA INTEGRATION</h3><p>Sed ut perspiciatis unde omnis ist<br>enatus error sit voluptatem</p></div>
<div class="overview-feature feature-left" style="left:60px;top:1286px"><h3>VALUATION</h3><p>Sed ut perspiciatis unde omnis<br>ist enatus error sit volupt</p></div>
<div class="overview-feature feature-left" style="left:128px;top:1438px"><h3>REGULATORY COMPILANCE</h3><p>Sed ut perspiciatis unde omnis ist<br>enatus error sit voluptatem</p></div>
<div class="overview-feature" style="left:817px;top:1133px"><h3>REPORTING &amp; INSIGHTS</h3><p>Sed ut perspiciatis unde omnis ist<br>enatus error sit voluptatem</p></div>
<div class="overview-feature" style="left:881px;top:1286px"><h3>RISK MANAGEMENT</h3><p>Sed ut perspiciatis unde omnis<br>ist enatus error sit volupta</p></div>
<div class="overview-feature" style="left:813px;top:1438px"><h3>MODELING &amp; ANALYSIS</h3><p>Sed ut perspiciatis unde omnis ist<br>enatus error sit voluptatem</p></div>

<div class="feature-icon" style="left:415px;top:1138px"><svg width="32" height="32" viewBox="0 0 32 32" fill="none" stroke="#0054AA" stroke-width="2"><rect x="4" y="4" width="10" height="10"/><rect x="18" y="4" width="10" height="10"/><path d="M9 14v6h14v-6M16 20v8"/></svg></div>
<div class="feature-icon" style="left:347px;top:1291px"><svg width="32" height="32" viewBox="0 0 32 32" fill="none" stroke="#0054AA" stroke-width="2"><path d="M4 28h24M8 24v-8M14 24V10M20 24v-6M26 24V6"/></svg></div>
<div class="feature-icon" style="left:415px;top:1443px"><svg width="32" height="32" viewBox="0 0 32 32" fill="none" stroke="#0054AA" stroke-width="2"><circle cx="16" cy="9" r="5"/><path d="M16 14v14M11 22h10"/></svg></div>
<div class="feature-icon" style="left:714px;top:1138px"><svg width="32" height="32" viewBox="0 0 32 32" fill="none" stroke="#0054AA" stroke-width="2"><circle cx="12" cy="12" r="7"/><path d="M17 17l9 9M9 14v-3M12 14V9M15 14v-2"/></svg></div>
<div class="feature-icon" style="left:783px;top:1291px"><svg width="32" height="32" viewBox="0 0 32 32" fill="none" stroke="#0054AA" stroke-width="2"><path d="M16 4l10 5v7c0 6-4 10-10 12C10 26 6 22 6 16V9z"/><path d="M11 16l4 4 6-7"/></svg></div>
<div class="feature-icon" style="left:714px;top:1443px"><svg width="32" height="32" viewBox="0 0 32 32" fill="none" stroke="#0054AA" stroke-width="2"><rect x="6" y="4" width="16" height="22" rx="2"/><path d="M10 10h8M10 15h8M10 20h4"/><circle cx="23" cy="23" r="4"/></svg></div>

<a class="btn" href="#" style="left:511px;top:1535px;width:178px;height:40px">Explore Platform</a>

<svg class="abs" style="left:0;top:1860px" width="1200" height="500" viewBox="0 0 1200 500"><path d="M0 420C300 250 700 240 1200 330V500H0Z" fill="#f2f4f7" opacity=".7"/></svg>

<h2 class="section-title" style="top:1697px">CORE SOLUTIONS</h2>
<p class="section-lead" style="top:1754px">Sed ut perspiciatis unde omnis iste natus error sit voluptatem accusantium doloremque laudantium, totam rem aperiam, eaque ipsa quae</p>

<article class="solution-card" style="left:112px">
  <div class="solution-icon"><svg width="40" height="40" viewBox="0 0 40 40" fill="none" stroke="#fff" stroke-width="2.2"><path d="M6 34h28M10 30V20M17 30V12M24 30V18M31 30V8"/></svg></div>
  <h3>RESERVING &amp; VALUATION</h3>
  <p>Software supporting structured reserving workflows and financial reporting across jurisdictions.</p>
</article>
<article class="solution-card featured" style="left:442px">
  <div class="solution-icon"><svg width="40" height="40" viewBox="0 0 40 40" fill="none" stroke="#fff" stroke-width="2.2"><path d="M20 6l12 12-14 14L6 20V6z"/><circle cx="13" cy="13" r="2.5"/></svg></div>
  <h3>PRICING</h3>
  <p>Models supporting insurance and reinsurance pricing based on actuarial methodologies.</p>
</article>
<article class="solution-card" style="left:772px">
  <div class="solution-icon"><svg width="40" height="40" viewBox="0 0 40 40" fill="none" stroke="#fff" stroke-width="2.2"><circle cx="20" cy="20" r="7"/><path d="M20 5v6M20 29v6M5 20h6M29 20h6M9 9l4 4M27 27l4 4M31 9l-4 4M13 27l-4 4"/></svg></div>
  <h3>ENTERPRISE<br>RISK MANAGEMENT</h3>
  <p>Software supporting reinsurance optimization and capital modeling.</p>
</article>

<section class="characteristics">
  <svg class="band" width="1200" height="772" viewBox="0 0 1200 772">
    <defs>
      <linearGradient id="charOrange" x1="0" y1="0" x2="1" y2="1">
        <stop offset="0" stop-color="#EE7325"/>
        <stop offset="1" stop-color="#E1521F"/>
      </linearGradient>
    </defs>
    <path d="M0 360C200 110 500 40 1200 70V772H0Z" fill="url(#charOrange)"/>
    <path d="M0 290C200 70 500 0 1200 20V70C500 40 200 110 0 360Z" fill="#0b3a9e"/>
    <path d="M0 260C200 50 500 -10 1200 10V24C500 8 200 70 0 290Z" fill="#0094D4"/>
    <path d="M440 80C520 300 620 420 760 480L820 470C680 400 580 280 520 80Z" fill="#F08F49" opacity=".4"/>
  </svg>
  <div class="visual-circle" role="img" aria-label="Photo of a magnifying glass over glowing financial bar charts"></div>
  <h2 class="char-title">OUR PLATFORM<br>CHARACTERISTICS</h2>
  <ul class="char-list">
    <li><svg width="16" height="16" viewBox="0 0 16 16"><circle cx="8" cy="8" r="8" fill="#fff"/><path d="M4.5 8.2l2.3 2.3 4.7-4.7" stroke="#EE7325" stroke-width="2" fill="none"/></svg>Structured workflows suitable for multi-jurisdictional review</li>
    <li><svg width="16" height="16" viewBox="0 0 16 16"><circle cx="8" cy="8" r="8" fill="#fff"/><path d="M4.5 8.2l2.3 2.3 4.7-4.7" stroke="#EE7325" stroke-width="2" fill="none"/></svg>Transparent assumptions and methodological clarity</li>
    <li><svg width="16" height="16" viewBox="0 0 16 16"><circle cx="8" cy="8" r="8" fill="#fff"/><path d="M4.5 8.2l2.3 2.3 4.7-4.7" stroke="#EE7325" stroke-width="2" fill="none"/></svg>Comparative scenario analysis</li>
    <li><svg width="16" height="16" viewBox="0 0 16 16"><circle cx="8" cy="8" r="8" fill="#fff"/><path d="M4.5 8.2l2.3 2.3 4.7-4.7" stroke="#EE7325" stroke-width="2" fill="none"/></svg>Supports professional judgment rather than replacing it</li>
  </ul>
</section>

<h2 class="section-title" style="top:3203px">OUR INSIGHTS</h2>
<p class="section-lead" style="top:3259px">Sed ut perspiciatis unde omnis iste natus error sit voluptatem accusantium doloremque laudantium, totam rem aperiam, eaque ipsa quae</p>

<article class="insight-card" style="left:114px">
  <div class="insight-media" role="img" aria-label="Photo of rows of dark data server blocks" style="background:linear-gradient(160deg,#3f6d8c,#14283c 70%)"></div>
  <span class="date-pill"><svg width="12" height="12" viewBox="0 0 12 12" fill="none" stroke="#fff" stroke-width="1.4"><rect x="1" y="2" width="10" height="9" rx="1"/><path d="M1 5h10"/></svg>03/13/2026</span>
  <h3>Methodological perspectives in actuarial reserving</h3>
  <p>Sed ut perspiciatis unde omnis iste natus error sit voluptatem..</p>
</article>
<article class="insight-card featured" style="left:446px">
  <div class="insight-media" role="img" aria-label="Photo of a magnifying glass over glowing question marks" style="background:radial-gradient(circle at 45% 40%,#3a8fe0,#0a2a66 70%)"></div>
  <span class="date-pill"><svg width="12" height="12" viewBox="0 0 12 12" fill="none" stroke="#fff" stroke-width="1.4"><rect x="1" y="2" width="10" height="9" rx="1"/><path d="M1 5h10"/></svg>03/13/2026</span>
  <h3>Governance considerations in multi-jurisdictional analysis</h3>
  <p>Sed ut perspiciatis unde omnis iste natus error sit voluptatem..</p>
</article>
<article class="insight-card" style="left:778px">
  <div class="insight-media" role="img" aria-label="Photo of digital document icons on a dark blue network" style="background:radial-gradient(circle at 50% 45%,#2e6ec4,#0a1f52 75%)"></div>
  <span class="date-pill"><svg width="12" height="12" viewBox="0 0 12 12" fill="none" stroke="#fff" stroke-width="1.4"><rect x="1" y="2" width="10" height="9" rx="1"/><path d="M1 5h10"/></svg>03/13/2026</span>
  <h3>Observations on actuarial practice in emerging markets</h3>
  <p>Sed ut perspiciatis unde omnis iste natus error sit voluptatem..</p>
</article>

<a class="btn" href="#" style="left:525px;top:3830px;width:150px;height:40px">Read Insights</a>

<svg class="abs" style="left:0;top:3900px" width="1200" height="560" viewBox="0 0 1200 560"><path d="M0 120C300 40 800 30 1200 110V560H0Z" fill="#f4f5f8" opacity=".8"/></svg>

<div class="cta-icon" role="img" aria-label="Illustration of a handshake"></div>
<h2 class="section-title cta-title">INTERESTED IN EXPLORING<br>THE PLATFORM?</h2>
<p class="section-lead" style="top:4247px">Sed ut perspiciatis unde omnis iste natus error sit voluptatem accusantium doloremque laudantium, totam rem aperiam, eaque ipsa quae</p>
<a class="btn" href="#" style="left:448px;top:4330px;width:305px;height:40px">Request a Technical Walkthrough</a>

<footer class="site-footer">
  <svg width="1200" height="507" viewBox="0 0 1200 507">
    <defs>
      <linearGradient id="footBlue" x1="0" y1="0" x2="0" y2="1">
        <stop offset="0" stop-color="#1a4fb0"/>
        <stop offset="1" stop-color="#0b2e86"/>
      </linearGradient>
    </defs>
    <path d="M0 150C300 70 800 50 1200 130V507H0Z" fill="url(#footBlue)"/>
    <path d="M0 150C300 70 800 50 1200 130V110C800 20 300 40 0 130Z" fill="#0094D4"/>
    <path d="M0 128C300 40 800 10 1200 108V80C800 -10 300 10 0 112Z" fill="#EE7325"/>
    <path d="M0 112C300 10 800 -10 1200 80V66C800 -20 300 -2 0 100Z" fill="#F0912C"/>
  </svg>
  <div class="footer-brand">QP Fiduciary</div>
  <nav class="footer-nav">
    <span style="left:226px">HOME</span>
    <span style="left:326px">COMPANY</span>
    <span style="left:458px">PLATFORM</span>
    <span style="left:597px">SOLUTIONS</span>
    <span style="left:741px">INSIGHTS</span>
    <span style="left:870px">CONTACT US</span>
  </nav>
  <div class="contact" style="left:205px">
    <span class="contact-icon"><svg width="16" height="16" viewBox="0 0 16 16" fill="#fff"><path d="M8 1a5 5 0 0 0-5 5c0 4 5 9 5 9s5-5 5-9a5 5 0 0 0-5-5zm0 7a2 2 0 1 1 0-4 2 2 0 0 1 0 4z"/></svg></span>
    <span>418 Harbor Crest Avenue, Suite 210<br>Lakeview, FL 30991</span>
  </div>
  <div class="contact" style="left:549px">
    <span class="contact-icon"><svg width="16" height="16" viewBox="0 0 16 16" fill="#fff"><path d="M3 1h3l1.5 4-2 1.3a9 9 0 0 0 4.2 4.2L11 8.5l4 1.5v3a2 2 0 0 1-2 2A12 12 0 0 1 1 3a2 2 0 0 1 2-2z"/></svg></span>
    <span>Call Us:<br>+1(555)014-2287</span>
  </div>
  <div class="contact" style="left:771px">
    <span class="contact-icon"><svg width="16" height="16" viewBox="0 0 16 16" fill="#fff"><path d="M1 3h14v10H1z"/><path d="M1 3l7 6 7-6" stroke="#E1521F" stroke-width="1.4" fill="none"/></svg></span>
    <span>Email Address:<br>contact@qp-fiduciary.example</span>
  </div>
  <a class="btn follow-btn" href="#">Follow us on: Our Network</a>
  <p class="copyright">(C) Copyright 2026 | All Rights Reserved</p>
</footer>

</body>
</html>
```